QVR business card

Need a business card for a company that provides instructional design and elearning development services. The website is here: http://quorvane.studio/

I'm attaching a current logo, as well as the old business card design. While I like to keep it clean, the old design is too simplistic for my liking. The only idea I want to reuse from the old design is placing industry jargon on the back of the card, just need a better way to present it. But if you have other ideas for the back--feel free to experiment.

Please use the colors complementary to the color we have on the website. Thank you!

```html
<!DOCTYPE html>
<html lang="en">
<head>
<meta charset="utf-8">
<title>QVR business card</title>
<link rel="stylesheet" href="https://fonts.googleapis.com/css2?family=Lato:wght@400;700&family=Josefin+Sans:wght@700&family=Archivo+Narrow:wght@700&display=swap">
<style>
  :root {
    --page: #e9e7e3;
    --card-white: #ffffff;
    --card-dark: #252628;
    --teal: #14b2ae;
    --teal-text: #16b0a6;
    --ink: #3a3a3a;
    --white: #ffffff;
  }
  * { box-sizing: border-box; margin: 0; padding: 0; }
  html, body {
    width: 1138px; height: 1200px; overflow: hidden;
    background: var(--page);
  }
  .canvas { position: relative; width: 1138px; height: 1200px; }

  .card {
    position: absolute; left: 233px; width: 672px; height: 384px;
    border-radius: 16px; overflow: hidden;
    box-shadow: 0 4px 14px rgba(0,0,0,0.25);
  }

  /* Front */
  .card-front { top: 198px; background: var(--card-white); }
  .brand {
    position: absolute; top: 56px; left: 0; right: 0;
    display: flex; align-items: center; justify-content: center; gap: 18px;
  }
  .brand-dot { width: 46px; height: 46px; border-radius: 50%; background: var(--teal); }
  .brand-name {
    font-family: "Lato", sans-serif; font-weight: 700;
    font-size: 64px; letter-spacing: 4px; color: var(--teal); line-height: 1;
  }
  .contact-band {
    position: absolute; top: 256px; left: 0; width: 100%; height: 95px;
    background: var(--teal); color: var(--white);
    font-family: "Lato", sans-serif;
  }
  .holder-name {
    position: absolute; left: 70px; top: 0; height: 95px;
    display: flex; align-items: center;
    font-weight: 700; font-size: 21px;
  }
  .divider {
    position: absolute; left: 288px; top: 10px; width: 1.5px; height: 75px;
    background: var(--white);
  }
  .contact-list {
    position: absolute; left: 302px; top: 9px; list-style: none;
    font-size: 18.5px; line-height: 23px;
  }
  .contact-list li { display: flex; align-items: center; gap: 8px; }
  .contact-list svg { width: 16px; height: 16px; flex: none; }

  /* Back */
  .card-back { top: 618px; background: var(--card-dark); height: 380px; }
  .jargon {
    position: absolute; left: 38px; width: 596px;
    display: flex; justify-content: space-between;
    font-family: "Josefin Sans", sans-serif; font-weight: 700;
    font-size: 35px; letter-spacing: 1.5px; color: var(--teal-text);
    line-height: 1;
  }
  .line-1 { top: 26px; }
  .line-2 { top: 74px; }
  .line-3 { top: 122px; }
  .line-4 { top: 236px; }
  .line-5 { top: 284px; }
  .line-6 { top: 332px; }
  .help-bar {
    position: absolute; top: 158px; left: 0; width: 100%; height: 58px;
  }
  .help-bar::before, .help-bar::after {
    content: ""; position: absolute; top: 0; width: 22px; height: 58px;
    background: var(--white);
  }
  .help-bar::before { left: 0; }
  .help-bar::after { right: 0; }
  .help-title {
    position: absolute; left: 38px; width: 596px; top: -4px;
    text-align: center;
    font-family: "Archivo Narrow", sans-serif; font-weight: 700;
    font-size: 66px; letter-spacing: -3.5px; color: var(--white); line-height: 1;
  }
</style>
</head>
<body>
<main class="canvas">
  <section class="card card-front">
    <div class="brand">
      <span class="brand-dot"></span>
      <span class="brand-name">QVR</span>
    </div>
    <div class="contact-band">
      <div class="holder-name">Marcus Delaney</div>
      <div class="divider"></div>
      <ul class="contact-list">
        <li>
          <svg viewBox="0 0 16 16" aria-hidden="true"><path d="M4 1.5l2.2 3-1.3 1.6c.8 1.8 2.2 3.3 4 4.2l1.5-1.3 3.1 2.1-1.2 2.6C6.4 13.8 1.9 8.6 1.6 2.8z" fill="#fff"/></svg>
          212-555-0148
        </li>
        <li>
          <svg viewBox="0 0 16 16" aria-hidden="true"><rect x="1" y="3" width="14" height="10" fill="none" stroke="#fff" stroke-width="1.4"/><path d="M1 3l7 6 7-6M1 13l5-5M15 13l-5-5" fill="none" stroke="#fff" stroke-width="1.2"/></svg>
          mdelaney@quorvane.studio
        </li>
        <li>
          <svg viewBox="0 0 16 16" aria-hidden="true"><g fill="none" stroke="#fff" stroke-width="1.2"><circle cx="8" cy="8" r="6.5"/><ellipse cx="8" cy="8" rx="3" ry="6.5"/><path d="M1.5 8h13M2.5 4.7h11M2.5 11.3h11"/></g></svg>
          www.quorvane.studio
        </li>
      </ul>
    </div>
  </section>

  <section class="card card-back">
    <div class="jargon line-1"><span>MOBILE</span><span>LEARNING</span><span>SCORM</span></div>
    <div class="jargon line-2"><span>INSTRUCTIONAL</span><span>DESIGN</span><span>LMS</span></div>
    <div class="jargon line-3"><span>MOOCS</span><span>ELEARNING</span><span>HTML5</span></div>
    <div class="help-bar"><h1 class="help-title">HOW CAN WE HELP?</h1></div>
    <div class="jargon line-4"><span>ADULT</span><span>LEARNING</span><span>THEORY</span></div>
    <div class="jargon line-5"><span>GAMIFICATION</span><span>CLASSROOM</span></div>
    <div class="jargon line-6"><span>XAPI</span><span>BLENDED</span><span>LEARNING</span></div>
  </section>
</main>
</body>
</html>
```